We need a Word Template for Custom Laboratory Results from an independent laboratory

The test is a novel biomarker for a chronic pain condition called endometriosis. It is expressed as a percentage. We will upload a sample result. We are looking for improved graphic fidelity with more attention to design and spacing. Emphasis should be placed on the overall result, i.e. the patient percentage results. Considerationis going to be given to the most appealing graphic result.

Target Market(s)

Women aged 19-45

Colors
0054AA
0677BA
7BADD7
CADEEF
E8F1F8

```html
<!DOCTYPE html>
<html lang="en">
<head>
<meta charset="utf-8">
<title>EndoSIG Endometriosis Assay Results</title>
<link href="https://fonts.googleapis.com/css2?family=Montserrat:wght@400;500;600;700&display=swap" rel="stylesheet">
<style>
  :root {
    --ink-deep: #0054AA;
    --ink-main: #0677BA;
    --ink-title: #1570A6;
    --ink-soft: #7BADD7;
    --tint: #CADEEF;
    --tint-light: #E8F1F8;
    --text-grey: #3c3c3c;
    --panel-grey: #EDEDED;
    --backdrop: #FFFFFF;
  }
  * { box-sizing: border-box; margin: 0; padding: 0; }
  html, body {
    width: 960px; height: 1200px; overflow: hidden;
    background: var(--backdrop);
    font-family: "Montserrat", sans-serif;
  }
  .sheet {
    position: absolute; left: 57px; top: 53px; width: 846px; height: 1094px;
    background: #fff;
    box-shadow: 0 0 22px rgba(0,0,0,0.10);
  }
  .brand-row {
    position: absolute; left: 40px; top: 98px;
    display: flex; align-items: center; gap: 52px;
  }
  .brand { display: flex; align-items: center; gap: 10px; font-weight: 500; font-size: 20px; color: var(--ink-main); }
  .brand-dot { width: 36px; height: 36px; border-radius: 50%; background: var(--tint); }
  .brand--partner { color: var(--ink-deep); font-size: 26px; }
  .title { position: absolute; left: 40px; top: 214px; color: var(--ink-title); line-height: 1.15; }
  .title-line { display: block; font-weight: 400; font-size: 39px; letter-spacing: 0.5px; }
  .title-line--strong { font-weight: 700; font-size: 41px; letter-spacing: 0.8px; }
  .results-band {
    position: absolute; left: 40px; top: 338px; width: 767px; height: 46px;
    background: var(--ink-main); color: #fff;
    font-weight: 700; font-size: 18px; letter-spacing: 0.3px;
    padding: 13px 0 0 32px;
  }
  .patient { position: absolute; left: 71px; top: 426px; list-style: none;
    font-weight: 700; font-size: 12.5px; color: var(--text-grey); letter-spacing: 0.3px; }
  .patient li { height: 34.5px; }
  .patient .pair span + span { margin-left: 30px; }
  .score-box {
    position: absolute; top: 547px; height: 121px;
    background: linear-gradient(to bottom, #f3f8fb 0%, #d6e6ee 100%);
  }
  .score-label { left: 41px; width: 422px; text-align: center; padding-top: 28px; color: var(--ink-main); font-size: 16.5px; line-height: 26px; }
  .score-label strong { font-weight: 700; }
  .score-value { left: 474px; width: 333px; display: flex; align-items: center; justify-content: center;
    color: var(--ink-main); font-weight: 700; font-size: 64px; }
  .divider { position: absolute; left: 40px; top: 725px; width: 767px; height: 1px; background: var(--ink-soft); }
  .reference {
    position: absolute; left: 41px; top: 780px; width: 766px; height: 235px;
    background: var(--panel-grey); padding: 30px 0 0 30px; color: var(--ink-main);
  }
  .reference-title { font-weight: 600; font-size: 19px; letter-spacing: 0.4px; margin-bottom: 12px; }
  .reference-list { list-style: none; font-size: 16.5px; }
  .reference-list li { height: 31.8px; display: flex; }
  .range { font-weight: 700; width: 122px; padding-left: 3px; }
</style>
</head>
<body>
  <main class="sheet">
    <header class="brand-row">
      <div class="brand"><span class="brand-dot"></span>Northvale Fertility</div>
      <div class="brand brand--partner">Corvian</div>
    </header>

    <h1 class="title">
      <span class="title-line">ENDOSIG MICRO-RNA</span>
      <span class="title-line title-line--strong">ENDOMETRIOSIS ASSAY</span>
    </h1>

    <div class="results-band">YOUR RESULTS</div>

    <ul class="patient">
      <li class="pair"><span>[FIRST NAME]</span><span>[LAST NAME]</span></li>
      <li>[HEALTH CARD NUMBER (12 CHARACTERS)]</li>
      <li>[DOB]</li>
    </ul>

    <div class="score-box score-label">
      <strong>Predicted probability of endometreosis</strong><br>
      Compared to<br>
      <strong>Surgical Controls (100% Probability)</strong>
    </div>
    <div class="score-box score-value">38.7%</div>

    <div class="divider"></div>

    <section class="reference">
      <h2 class="reference-title">REFERENCE RANGE</h2>
      <ul class="reference-list">
        <li><span class="range">0.0 - 29.9%</span><span>- low probability of endometriosis</span></li>
        <li><span class="range">29.9 - 44.9%</span><span>- inconclusive</span></li>
        <li><span class="range">45.0 - 55.0%</span><span>- intermediate risk of endometriosis</span></li>
        <li><span class="range">55.1 - 64.9%</span><span>- probable endometriosis</span></li>
        <li><span class="range">65.0 - 99.9%</span><span>- highly probable endometriosis</span></li>
      </ul>
    </section>
  </main>
</body>
</html>
```